Buch-/eBook-Cover für Geschichte zum Pride auf Gran Canaria
Zielgruppe
Zielgruppe: Reisefreudige junge schwule Männer
Aufgabenstellung
Die Geschichte spielt zum Pride auf Gran Canaria. Es geht um vier Freunde die dort ihre Ferien verbingen.
Ich stelle mir vor, dass auf dem Cover die Regenbogenflagge ist, Strand, Meer, keine Menschen und ein fetter Schriftzug mit dem Titel #TorvilenaGlanz. Daneben sollte kleiner mein Name Ferdinand zu Brakwede stehen. Das Cover kann aber auch gern wie ein Partyflyer designt sein und der Titel wie ein Logo wirken.
Bin aber für alternativen offen.

```html
<!DOCTYPE html>
<html lang="de">
<head>
<meta charset="utf-8">
<title>#TorvilenaGlanz – Buchcover</title>
<link rel="stylesheet" href="https://fonts.googleapis.com/css2?family=Noto+Serif:wght@400;500&family=Titan+One&display=swap">
<style>
  :root {
    --stage: #e9e6ee;
    --sky-deep: #2752b8;
    --sky: #4a8ddf;
    --flag-red: #d8324a;
    --flag-orange: #ee8a2c;
    --flag-yellow: #f4d43c;
    --flag-green: #3fa85a;
    --flag-blue: #3a66d0;
    --flag-violet: #7a3fb0;
    --band: #f3eff8;
    --sea: #3f86c4;
    --sun: #fff4dc;
    --sand: #e4a370;
    --sand-dark: #a95e39;
    --title: #7b3fa8;
    --white: #ffffff;
  }
  * { margin: 0; padding: 0; box-sizing: border-box; }
  html, body { width: 1200px; height: 846px; overflow: hidden; }
  body {
    background: var(--stage);
    display: flex;
    align-items: center;
    justify-content: center;
  }
  .book-cover {
    position: relative;
    width: 524px;
    height: 760px;
    overflow: hidden;
    box-shadow: 0 10px 30px rgba(40, 30, 70, 0.18);
  }
  .cover-artwork {
    position: absolute;
    inset: 0;
    background:
      radial-gradient(ellipse 70% 18% at 50% 73%, var(--sun) 0%, rgba(255,244,220,0) 70%),
      linear-gradient(180deg,
        var(--sky-deep) 0%,
        var(--sky) 7%,
        var(--flag-red) 14%,
        var(--flag-orange) 22%,
        var(--flag-yellow) 29%,
        var(--flag-green) 36%,
        var(--flag-blue) 43%,
        var(--flag-violet) 48%,
        var(--band) 53%,
        var(--band) 58%,
        var(--sky) 63%,
        var(--sea) 68%,
        var(--sun) 73%,
        var(--sea) 79%,
        var(--sand) 86%,
        var(--sand-dark) 100%);
  }
  .author-name {
    position: absolute;
    top: 52px;
    left: 0;
    right: 0;
    text-align: center;
    font-family: "Noto Serif", serif;
    font-weight: 500;
    font-size: 19px;
    letter-spacing: 0.5px;
    color: var(--white);
    text-transform: uppercase;
  }
  .book-title {
    position: absolute;
    top: 376px;
    left: 0;
    right: 0;
    text-align: center;
    font-family: "Titan One", sans-serif;
    font-weight: 400;
    font-size: 52px;
    line-height: 1;
    letter-spacing: 0.5px;
    color: var(--title);
    text-transform: uppercase;
  }
  .book-subtitle {
    position: absolute;
    top: 515px;
    left: 280px;
    font-family: "Noto Serif", serif;
    font-size: 17px;
    color: var(--white);
    text-transform: uppercase;
  }
</style>
</head>
<body>
  <main class="book-cover">
    <div class="cover-artwork" role="img" aria-label="Illustration: wehende Regenbogenflagge wie Flügel mit rotem Herz, weißes Papierband, Meer im Sonnenlicht und Sandstrand"></div>
    <p class="author-name">Ferdinand zu Brakwede</p>
    <h1 class="book-title">#TorvilenaGlanz</h1>
    <p class="book-subtitle">Platz für Untertitel</p>
  </main>
</body>
</html>
```